Quality Monitoring Company Needs a New Site

We are an established company that has a fair number of clients but the site lacks current design standards that we'd like to keep up with. We'd like to mimic the same style of the site on plinkora.com, vetrumo.com, https://brindlecoffer.com/, etc. We'd also like to make sure the designer understands SEO Silos and how it effects the design elements. Attached is the structure that I'd like to follow for the pages. You don't need to design every single sub-page because they'll probably be fairly similar; however, I want to see at least 1 each. Please use the content on our current site for filler areas. Please try to do a good job of understanding what we do so you can use your best judgement on what is needed to be successful. Use our color scheme and the logo should be the side view but I included the AI just in case.
Updates

I am narrowing down on the field of designs that I have received. There are a lot of similarities between the designs I like and don't like. I'd also like to ensure that some of the inner pages get done in the next 5 days so I can see the creativity that is there as well. That is probably what is next -- getting a few inner pages completed so I can see what you can come up with (not based on our current website) because the current "front pages" are all so good and so close.

Industry/Entity Type

Telecommunications

Colors

Designer to choose colors to be used in the design.

Requirements
Must have
• SEO Silo Look and Feel
• Current Colors
Should not have
• No stockphotos whatsoever. NONE.

```html
<!DOCTYPE html>
<html lang="en">
<head>
<meta charset="utf-8">
<title>Tallyreach — Call Center Quality Monitoring</title>
<link href="https://fonts.googleapis.com/css2?family=Raleway:wght@400;500&family=Roboto:wght@400;500;700&display=swap" rel="stylesheet">
<style>
:root{
  --navy:#0d2a4e;
  --blue:#1aa3df;
  --btn-top:#0b5e97;
  --btn-bot:#053461;
  --text:#6b6b6b;
  --dark:#151515;
  --ice:#dff0fa;
  --ice-2:#c8e4f5;
  --footer:#2b2b2b;
  --line:#d6d6d6;
}
*{box-sizing:border-box;margin:0;padding:0}
html,body{width:1200px;height:3327px;overflow:hidden}
body{position:relative;background:#fff;font-family:'Roboto',sans-serif;color:var(--text)}
.abs{position:absolute}
.heading{font-family:'Raleway',sans-serif;font-weight:400;color:var(--navy);font-size:42px;letter-spacing:.3px}
.heading span{color:var(--blue)}
.center{left:0;width:1200px;text-align:center}
.btn{position:absolute;display:flex;align-items:center;justify-content:center;gap:10px;color:#fff;font-weight:700;font-size:16px;background:linear-gradient(var(--btn-top),var(--btn-bot));text-transform:uppercase;letter-spacing:.2px}
.btn svg{width:16px;height:16px}
/* header */
.logo{font-family:'Raleway',sans-serif;font-weight:500;font-size:40px;color:var(--navy);letter-spacing:-.5px}
.nav{position:absolute;top:40px;left:384px;display:flex;gap:27px;font-size:14.5px;font-weight:500;color:var(--dark)}
.nav .on{color:var(--blue);position:relative}
.nav .on:after{content:"";position:absolute;left:0;right:0;top:26px;height:3px;background:var(--blue)}
/* services */
.service{position:absolute;top:720px;width:300px;text-align:center}
.service svg{width:78px;height:78px}
.service h3{margin-top:18px;font-size:19px;font-weight:500;color:var(--dark);letter-spacing:.3px}
.service p{margin-top:8px;font-size:15px;line-height:26px}
.arrow{position:absolute;width:48px;height:48px;border-radius:50%;border:1px solid #bbb;background:#fff;display:flex;align-items:center;justify-content:center}
.arrow svg{width:18px;height:18px}
/* team */
.team-band{top:1460px;left:0;width:1200px;height:523px;background:radial-gradient(circle at 20% 30%,#f4faff 0,transparent 40%),radial-gradient(circle at 80% 70%,#eef7fd 0,transparent 40%),linear-gradient(135deg,var(--ice),#eaf5fc 50%,var(--ice-2))}
.member{position:absolute;top:1650px;width:304px;height:232px;background:#fff;border-radius:12px;box-shadow:0 2px 8px rgba(0,0,0,.12);text-align:center}
.avatar{position:absolute;left:97px;top:-10px;width:112px;height:112px;border-radius:50%;background:#fff;box-shadow:0 2px 6px rgba(0,0,0,.12);display:flex;align-items:center;justify-content:center}
.avatar div{width:62px;height:62px;border-radius:50%;background:#f0d6c2}
.member h3{position:absolute;top:118px;left:0;right:0;font-size:24px;font-weight:500;color:var(--dark)}
.member p{position:absolute;top:158px;left:30px;right:30px;font-size:15px;line-height:26px}
/* blog */
.post{position:absolute;top:2183px;width:315px;height:379px;background:#fff;box-shadow:0 0 6px rgba(0,0,0,.16);text-align:center}
.post .date{margin-top:32px;display:flex;justify-content:center;align-items:center;gap:12px;color:var(--blue);font-weight:500;font-size:19px}
.post h3{margin-top:26px;font-size:19px;font-weight:500;color:var(--dark)}
.post p{margin:20px 20px 0;font-size:15px;line-height:26px}
.post .btn{left:69px;top:296px;width:177px;height:52px}
.dots{top:2604px;left:568px;display:flex;gap:10px}
.dots i{width:14px;height:14px;border-radius:50%;background:var(--blue);border:1.5px solid var(--blue)}
.dots i.off{background:#fff}
/* contact */
.contact-band{top:2692px;left:0;width:1200px;height:438px;background:linear-gradient(135deg,#cfe6f5,#eaf5fc 45%,#d8ecf8)}
.field{position:absolute;background:#fff;font-size:16px;color:#555;padding:14px 10px}
.info{position:absolute;left:752px;display:flex;align-items:center;gap:30px;font-size:16px;color:var(--dark);line-height:26px}
.info .ring{width:46px;height:46px;border-radius:50%;border:1px solid #9ccbe9;display:flex;align-items:center;justify-content:center}
.info svg{width:20px;height:20px}
/* footer */
.footer{top:3130px;left:0;width:1200px;height:197px;background:var(--footer);color:#fff}
.flinks{position:absolute;left:393px;top:80px;font-size:16px;display:flex;gap:14px}
</style>
</head>
<body>

<!-- header -->
<div class="abs logo" style="left:113px;top:22px">Tallyreach</div>
<nav class="nav">
  <span class="on">HOME</span><span>ABOUT US</span><span>SERVICES</span><span>TEAM</span><span>CONTACT US</span><span>BLOG</span>
</nav>
<div class="btn" style="left:933px;top:22px;width:126px;height:52px">LOG IN
  <svg viewBox="0 0 16 16"><rect x="3" y="7" width="10" height="8" fill="#fff"/><path d="M5 7V5a3 3 0 0 1 6 0v2" stroke="#fff" stroke-width="2" fill="none"/></svg></div>

<!-- hero -->
<div class="abs" role="img" aria-label="Illustration of a person on the phone beside an office desk with a monitor and chair, on a pale blue blob" style="left:4px;top:126px;width:594px;height:404px;border-radius:46% 54% 40% 60%/55% 45% 55% 45%;background:linear-gradient(135deg,#dff3fb,#cdebf8)"></div>
<div class="abs heading" style="left:660px;top:228px;font-size:50px">Tallyreach</div>
<p class="abs" style="left:661px;top:300px;width:418px;font-size:15px;line-height:26px;text-align:justify">Tallyreach is committed to providing call centers of all shapes and sizes with the essential tools.</p>
<div class="btn" style="left:662px;top:368px;width:179px;height:52px">VIEW PRICING <svg viewBox="0 0 16 16"><circle cx="8" cy="8" r="8" fill="#fff"/><path d="M5 8h6M8 5l3 3-3 3" stroke="#053461" stroke-width="2" fill="none"/></svg></div>

<!-- services -->
<div class="abs heading center" style="top:618px">Our <span>Services</span></div>
<div class="arrow" style="left:28px;top:830px"><svg viewBox="0 0 18 18"><path d="M12 2 5 9l7 7" stroke="#111" stroke-width="2.4" fill="none"/></svg></div>
<div class="arrow" style="left:1117px;top:830px"><svg viewBox="0 0 18 18"><path d="M6 2l7 7-7 7" stroke="#111" stroke-width="2.4" fill="none"/></svg></div>
<div class="service" style="left:102px">
  <svg viewBox="0 0 78 78" fill="none" stroke="#1a6fb0" stroke-width="2"><circle cx="24" cy="24" r="14"/><circle cx="24" cy="24" r="6"/><path d="M44 30l16 6v14c0 10-8 16-16 19-8-3-16-9-16-19V36z"/><path d="M37 49l5 5 10-10"/></svg>
  <h3>QUALITY ASSURANCE</h3>
  <p>Lorem ipsum dolor sit amet, consectetur adipiscing elit, sed eiusmod tempor incididunt ut labore.</p></div>
<div class="service" style="left:450px">
  <svg viewBox="0 0 78 78" fill="none" stroke="#1a6fb0" stroke-width="2"><rect x="14" y="12" width="50" height="46" rx="3"/><path d="M22 22h34M22 30h34M22 38h20"/><path d="M8 66h62M20 58v8M58 58v8"/></svg>
  <h3>COACHING</h3>
  <p>Lorem ipsum dolor sit amet, consectetur adipiscing elit, sed eiusmod tempor incididunt ut labore.</p></div>
<div class="service" style="left:797px">
  <svg viewBox="0 0 78 78" fill="none" stroke="#1a6fb0" stroke-width="2"><rect x="6" y="10" width="40" height="32" stroke-dasharray="4 3"/><path d="M20 34l14-18"/><circle cx="21" cy="19" r="3"/><circle cx="33" cy="31" r="3"/><rect x="28" y="40" width="44" height="28"/><path d="M36 54h28"/></svg>
  <h3>SALES PERFORMANCE</h3>
  <p>Lorem ipsum dolor sit amet, consectetur adipiscing elit, sed eiusmod tempor incididunt ut labore.</p></div>

<!-- industries -->
<div class="abs heading" style="left:111px;top:1056px">Indu<span>stries</span></div>
<p class="abs" style="left:113px;top:1124px;width:428px;font-size:15px;line-height:26px;text-align:justify">Sed ut perspiciatis unde omnis iste natus error sit voluptatem accusantium doloremque laudantium, totam rem aperiam, eaque ipsa quae ab illo inventore veritatis et quasi architecto beatae vitae dicta sunt explicabo. Nemo enim ipsam voluptatem quia voluptas sit aspernatur.</p>
<div class="btn" style="left:115px;top:1279px;width:152px;height:52px">VIEW ALL <svg viewBox="0 0 16 16"><circle cx="8" cy="8" r="8" fill="#fff"/><path d="M5 8h6M8 5l3 3-3 3" stroke="#053461" stroke-width="2" fill="none"/></svg></div>
<div class="abs" role="img" aria-label="Illustration of a laptop showing a report, in front of faint gears and a globe" style="left:615px;top:1025px;width:465px;height:315px;border-radius:40% 50% 30% 30%;background:linear-gradient(135deg,#f2f7fb,#d3e4f1)"></div>

<!-- team -->
<div class="abs team-band"></div>
<div class="abs heading center" style="top:1532px">Our <span>Team</span></div>
<div class="arrow" style="left:26px;top:1742px"><svg viewBox="0 0 18 18"><path d="M12 2 5 9l7 7" stroke="#111" stroke-width="2.4" fill="none"/></svg></div>
<div class="arrow" style="left:1117px;top:1742px"><svg viewBox="0 0 18 18"><path d="M6 2l7 7-7 7" stroke="#111" stroke-width="2.4" fill="none"/></svg></div>
<div class="member" style="left:112px"><div class="avatar" role="img" aria-label="Avatar illustration of Owen Carrick"><div></div></div><h3>OWEN CARRICK</h3><p>Ut enim ad minima veniam, quis nostrum exercitationem.</p></div>
<div class="member" style="left:446px"><div class="avatar" role="img" aria-label="Avatar illustration of Lena Harwick"><div></div></div><h3>LENA HARWICK</h3><p>Ut enim ad minima veniam, quis nostrum exercitationem.</p></div>
<div class="member" style="left:781px"><div class="avatar" role="img" aria-label="Avatar illustration of Priya"><div></div></div><h3>PRIYA</h3><p>Ut enim ad minima veniam, quis nostrum exercitationem.</p></div>

<!-- blog -->
<div class="abs heading center" style="top:2064px">Our <span>Blog</span></div>
<div class="post" style="left:113px">
  <div class="date"><svg width="20" height="20" viewBox="0 0 20 20" fill="none" stroke="#1aa3df" stroke-width="1.8"><rect x="2" y="4" width="16" height="14"/><path d="M2 8h16M6 2v4M14 2v4M6 11h2M10 11h2M14 11h1M6 14h2M10 14h2"/></svg>19 OCTOBER 2019</div>
  <h3>CALL CENTER SKILLS</h3>
  <p>We all know the importance of inbound call centers when it comes to customer service. They are the places that everyone calls when they have a problem with anything from computer software to vacuum cleaners.</p>
  <div class="btn">READ MORE <svg viewBox="0 0 16 16"><circle cx="8" cy="8" r="8" fill="#fff"/><path d="M5 8h6M8 5l3 3-3 3" stroke="#053461" stroke-width="2" fill="none"/></svg></div></div>
<div class="post" style="left:442px">
  <div class="date"><svg width="20" height="20" viewBox="0 0 20 20" fill="none" stroke="#1aa3df" stroke-width="1.8"><rect x="2" y="4" width="16" height="14"/><path d="M2 8h16M6 2v4M14 2v4M6 11h2M10 11h2M14 11h1M6 14h2M10 14h2"/></svg>20 OCTOBER 2019</div>
  <h3>PRODUCT</h3>
  <p>First of all, we are going to take a look at what a product is in a call center. The reason for this is because the dictionary definition of “product” is this: Something that is made to be sold, usually something that is produced.</p>
  <div class="btn">READ MORE <svg viewBox="0 0 16 16"><circle cx="8" cy="8" r="8" fill="#fff"/><path d="M5 8h6M8 5l3 3-3 3" stroke="#053461" stroke-width="2" fill="none"/></svg></div></div>
<div class="post" style="left:771px">
  <div class="date"><svg width="20" height="20" viewBox="0 0 20 20" fill="none" stroke="#1aa3df" stroke-width="1.8"><rect x="2" y="4" width="16" height="14"/><path d="M2 8h16M6 2v4M14 2v4M6 11h2M10 11h2M14 11h1M6 14h2M10 14h2"/></svg>21 OCTOBER 2019</div>
  <h3>CALL CENTER COACHING</h3>
  <p>Call Center Agents can be under a lot of pressure to perform to all of the criteria that you have in place. All of which are required to get the best service for your customers. However, some Agents can find it challenging.</p>
  <div class="btn">READ MORE <svg viewBox="0 0 16 16"><circle cx="8" cy="8" r="8" fill="#fff"/><path d="M5 8h6M8 5l3 3-3 3" stroke="#053461" stroke-width="2" fill="none"/></svg></div></div>
<div class="abs dots"><i></i><i class="off"></i><i></i></div>

<!-- contact -->
<div class="abs contact-band"></div>
<div class="abs heading" style="left:110px;top:2748px">Contact <span>Us</span></div>
<div class="field" style="left:111px;top:2826px;width:275px;height:42px">First Name</div>
<div class="field" style="left:399px;top:2826px;width:275px;height:42px">Last Name</div>
<div class="field" style="left:111px;top:2885px;width:275px;height:42px">Email</div>
<div class="field" style="left:399px;top:2885px;width:275px;height:42px">Phone No</div>
<div class="field" style="left:111px;top:2943px;width:563px;height:78px">Message</div>
<div class="btn" style="left:111px;top:3035px;width:170px;height:44px">SUBMIT NOW <svg viewBox="0 0 16 16"><circle cx="8" cy="8" r="8" fill="#fff"/><path d="M5 8h6M8 5l3 3-3 3" stroke="#053461" stroke-width="2" fill="none"/></svg></div>
<div class="info" style="top:2826px"><div class="ring"><svg viewBox="0 0 20 20" fill="none" stroke="#1aa3df" stroke-width="1.8"><path d="M10 19s6-6 6-11a6 6 0 0 0-12 0c0 5 6 11 6 11z"/><circle cx="10" cy="8" r="2"/></svg></div><div>4810 Marlowe Ave.<br>Brookfield, OR 97402</div></div>
<div class="info" style="top:2899px"><div class="ring"><svg viewBox="0 0 20 20" fill="none" stroke="#1aa3df" stroke-width="1.8"><path d="M4 2h4l1 5-2 1c1 2 3 4 5 5l1-2 5 1v4c0 1-1 2-2 2C9 18 2 11 2 4c0-1 1-2 2-2z"/></svg></div><div>555-214-7730</div></div>
<div class="info" style="top:2971px"><div class="ring"><svg viewBox="0 0 20 20" fill="none" stroke="#1aa3df" stroke-width="1.8"><rect x="2" y="4" width="16" height="12"/><path d="M2 4l8 7 8-7"/></svg></div><div>hello(at)tallyreach.com</div></div>

<!-- footer -->
<footer class="abs footer">
  <div class="abs logo" style="left:114px;top:42px;color:#fff">Tallyreach</div>
  <p class="abs" style="left:111px;top:98px;width:228px;font-size:14.5px;line-height:24px;text-align:justify;color:#fff">Lorem ipsum dolor sit amet, consectetur adipiscing elit, sed do eiusmod tempor.</p>
  <div class="flinks"><span>Home</span>/<span>Industries</span>/<span>Contact Us</span>/<span>Latest News</span>/<span>Services</span>/<span>About us</span>/<span>Reviews</span></div>
  <div class="abs" style="left:395px;top:118px;width:692px;height:1px;background:#555"></div>
  <div class="abs" style="left:395px;top:142px;width:692px;text-align:center;font-size:16px">© 2019 Tallyreach. All Rights Reserved</div>
</footer>

</body>
</html>
```